The Linen Loft Co

We need a business card design for our wardrobe company.
Please visit our website www.gentlelinenlofts.com to get an idea of who we are.

```html
<!DOCTYPE html>
<html lang="en">
<head>
<meta charset="UTF-8">
<title>The Linen Loft Co — Business Card</title>
<link href="https://fonts.googleapis.com/css2?family=Poppins:wght@400;500;600&display=swap" rel="stylesheet">
<style>
  :root {
    --backdrop: #2a2a2a;
    --card: #ffffff;
    --ink: #111111;
    --ink-soft: #4a4a4a;
    --muted: #a6a6a6;
  }
  * { margin: 0; padding: 0; box-sizing: border-box; }
  html, body {
    width: 1200px;
    height: 800px;
    overflow: hidden;
    background: var(--backdrop);
    font-family: "Poppins", sans-serif;
  }
  .card {
    position: absolute;
    left: 100px;
    top: 125px;
    width: 1000px;
    height: 550px;
    background: var(--card);
    color: var(--ink);
  }
  .brand {
    position: absolute;
    left: 58px;
    top: 74px;
    display: flex;
    align-items: center;
    gap: 20px;
  }
  .brand-mark {
    width: 62px;
    height: 62px;
    background: var(--ink);
  }
  .brand-name {
    font-size: 21px;
    font-weight: 500;
    letter-spacing: 0.2px;
    text-transform: uppercase;
    line-height: 1.2;
  }
  .brand-tagline {
    font-size: 18px;
    font-weight: 500;
    margin-top: 8px;
    margin-left: 26px;
  }
  .person {
    position: absolute;
    left: 55px;
    top: 372px;
  }
  .person-name {
    font-size: 36px;
    font-weight: 500;
    line-height: 1.1;
  }
  .person-role {
    font-size: 23px;
    font-weight: 400;
    color: var(--muted);
    line-height: 1.2;
  }
  .contact {
    position: absolute;
    left: 515px;
    top: 332px;
    font-size: 22px;
    line-height: 30px;
    color: var(--ink-soft);
  }
  .contact-address { margin-bottom: 15px; }
  .contact-lines { color: #333333; margin-left: 3px; }
</style>
</head>
<body>
  <div class="card">
    <div class="brand">
      <div class="brand-mark"></div>
      <div class="brand-text">
        <div class="brand-name">The Linen Loft Co</div>
        <div class="brand-tagline">Crafted for Calm Spaces</div>
      </div>
    </div>

    <div class="person">
      <div class="person-name">Daniel Hartley</div>
      <div class="person-role">President</div>
    </div>

    <div class="contact">
      <div class="contact-address">
        Orchard Court, 42 Mill Lane,<br>
        London N7 4QT
      </div>
      <div class="contact-lines">
        P. 020 7946 0318<br>
        info@gentlelinenlofts.com<br>
        www.gentlelinenlofts.com
      </div>
    </div>
  </div>
</body>
</html>
```